Brandwyn Fuel Retro Website Design

Have a logo. Need a website design to go along with the logo design. Full Design Specs are here: https://files.plinverdocs.net/sheet/d/8QmRtZxWv3-41pk527LNB_XY4HaPcOdsuw2K-rb6/view

Target Market(s)

Independent Gas Station Owners

Number of Pages Required

1 page

Font styles to use
Sans Serif

Colors

Designer to choose colors to be used in the design.

```html
<!DOCTYPE html>
<html lang="en">
<head>
<meta charset="utf-8">
<title>Brandwyn Fuel</title>
<link href="https://fonts.googleapis.com/css2?family=Roboto:wght@300;400;500;700&display=swap" rel="stylesheet">
<style>
:root{
  --paper:#f1dcae;
  --paper-dark:#e3c48c;
  --red:#e0131f;
  --ink:#1e1e1e;
  --charcoal:#3e3e3e;
  --white:#ffffff;
}
*{box-sizing:border-box;margin:0;padding:0}
html,body{width:1200px;height:3865px;overflow:hidden}
body{font-family:'Roboto',sans-serif;color:var(--ink);
  background:radial-gradient(ellipse at 50% 30%,#f6e5bd 0%,var(--paper) 45%,var(--paper-dark) 100%);position:relative}
.abs{position:absolute}
.center{left:0;width:1200px;text-align:center}
.header{top:0;left:0;width:1200px;height:180px}
.search{left:160px;top:36px;width:250px;height:42px;border:2px solid #555;border-radius:21px;background:#f7ead0;font-size:13px;color:#777;padding:12px 16px}
.search .btn{position:absolute;right:4px;top:4px;width:30px;height:30px;border-radius:50%;background:#333}
.nav{top:116px;font-size:16px;font-weight:500}
.nav span{position:absolute;white-space:nowrap}
.brand-name{font-weight:700;color:var(--ink);text-align:center;white-space:nowrap}
.call{left:800px;top:33px}
.call small{display:block;color:var(--red);font-size:14px;margin-left:48px}
.call strong{display:block;font-size:22px;font-weight:400;margin-left:48px;color:#333}
.hero{top:180px;left:0;width:1200px;height:650px;background:linear-gradient(180deg,#8c8c8c 0%,#b4b0a8 35%,#dcdad6 55%,#7a746c 100%)}
h2{font-weight:400;font-size:36px;color:var(--ink)}
h2 em{font-style:normal;color:var(--red);font-weight:500}
.body-text{font-size:15px;line-height:36px;color:var(--ink)}
.btn-pill{position:absolute;height:48px;border-radius:24px;color:var(--white);font-size:15px;font-weight:500;display:flex;align-items:center;justify-content:center;gap:10px}
.btn-pill i{width:15px;height:15px;border-radius:50%;background:var(--white);display:inline-block;position:relative}
.btn-pill i:after{content:"";position:absolute;left:4px;top:4px;border-left:7px solid;border-top:3.5px solid transparent;border-bottom:3.5px solid transparent}
.red{background:var(--red)}.red i:after{border-left-color:var(--red)}
.black{background:#111}.black i:after{border-left-color:#111}
.about{top:1247px;left:0;width:1200px;height:471px;background:linear-gradient(90deg,#cbb48a,#d9c497 50%,#e2cda2)}
.card{position:absolute;top:1938px;width:328px;height:216px}
.card .ph{height:171px}
.card .lab{height:45px;background:var(--red);color:var(--white);font-size:22px;font-weight:500;text-align:center;line-height:45px}
.employ{top:2280px;left:0;width:1200px;height:383px;background:linear-gradient(180deg,#c6ad7f,#d7c298 60%,#e4cfa6)}
.field{position:absolute;background:#fff;border:1px solid #e2d6be;font-size:12px;color:#555;padding:11px 18px}
.footer{top:3340px;left:0;width:1200px;height:525px;background:var(--charcoal)}
.ficon{position:absolute;top:3565px;width:80px;height:80px;border-radius:50%;background:radial-gradient(circle at 50% 40%,#e8323b,#b40d16)}
.ftext{position:absolute;top:3656px;width:300px;text-align:center;color:var(--white);font-size:18px;line-height:28px;font-weight:500}
.flinks{top:3732px;color:var(--white);font-size:15px;font-weight:500}
.copy{top:3776px;color:#ddd;font-size:14px}
.soc{position:absolute;top:3820px;width:28px;height:28px;border-radius:50%;border:2px solid #ddd}
</style>
</head>
<body>
<div class="abs header">
  <div class="abs search">Search<span class="btn"></span></div>
  <div class="abs brand-name" style="left:500px;top:76px;width:200px;font-size:26px">Brandwyn Fuel</div>
  <div class="abs call">
    <svg class="abs" style="left:0;top:4px" width="40" height="40" viewBox="0 0 40 40"><circle cx="20" cy="20" r="18" fill="none" stroke="#333" stroke-width="2.5"/><path d="M13 12c2-2 4 2 5 4s-2 3-1 5 3 4 5 4 3-3 5-1 3 4 1 5c-4 3-9 0-13-5s-5-10-2-12z" fill="#333"/></svg>
    <small>Call us today.</small><strong>888 888 8888</strong>
  </div>
  <div class="abs nav" style="left:0;width:1200px">
    <span style="left:89px">Home</span>
    <span style="left:160px">Our Company</span>
    <span style="left:287px">Employment Opportunities</span>
    <span style="left:724px">Products &amp; Services</span>
    <span style="left:898px">Contact Us</span>
    <span style="left:1006px">B's Containers</span>
  </div>
</div>

<div class="abs hero" role="img" aria-label="Photo of the fuel company's white metal storefront building with trucks parked in front"></div>
<div class="abs brand-name" style="left:786px;top:485px;width:280px;font-size:38px;color:var(--white)">Brandwyn Fuel</div>
<svg class="abs" style="left:0;top:700px" width="1200" height="160" viewBox="0 0 1200 160"><path d="M0 80 C150 50 300 110 450 70 C560 40 600 20 700 45 C820 80 950 60 1200 40 L1200 160 L0 160Z" fill="#f3e0b4"/></svg>

<h2 class="abs center" style="top:930px">Welcome to <em>BRANDWYN FUEL</em></h2>
<p class="abs center body-text" style="top:990px">Brandwyn Fuel provides the full-scale service of a petroleum distributor, delivering gasoline, diesel and lube oils to retail, commercial and farm<br>accounts.&nbsp; Our own fleet of delivery trucks provides distribution of fuel to several counties within the North Texas area.<br>Along with a knowledgeable and professional staff, Brandwyn Fuel makes customer service and satisfaction priority one.</p>
<div class="btn-pill red" style="left:411px;top:1119px;width:181px">READ MORE <i></i></div>
<div class="btn-pill black" style="left:606px;top:1119px;width:181px">CONTACT US <i></i></div>

<div class="abs about" role="img" aria-label="Faded sepia photo of a fuel tanker truck among bare trees"></div>
<div class="abs brand-name" style="left:115px;top:1455px;width:370px;font-size:48px">Brandwyn Fuel</div>
<h2 class="abs" style="left:528px;top:1335px">About <em>Brandwyn Fuel</em></h2>
<p class="abs body-text" style="left:528px;top:1385px;width:590px;font-size:14px;line-height:34px">The selling and servicing of petroleum products by Dale Brandwyn and Brandwyn Fuel<br>Company began in 1966 with the purchase of the Cedar County Ridgeway franchise<br>from Mr. Lowell Penner, the original Ridgeway commission agent since 1933.<br>As Brandwyn Fuel Company continues to grow and diversify, Our committment to Customer<br>Service &amp; Satisfaction will remain "Old School".</p>
<div class="btn-pill red" style="left:528px;top:1572px;width:182px">READ MORE <i></i></div>

<h2 class="abs center" style="top:1788px">Brandwyn Fuel <em>Products</em></h2>
<p class="abs center body-text" style="top:1842px">Lorem ipsum dolor sit amet, consectetur adipiscing elit, sed do eiusmod tempor incididunt ut labore et dolore magna aliqua. Quis ipsum<br>suspendisse ultrices gravida. Risus commodo viverra maecenas accumsan lacus vel facilisis.</p>
<div class="card" style="left:90px"><div class="ph" role="img" aria-label="Photo of white semi fuel delivery trucks" style="background:linear-gradient(180deg,#a7a7a7,#d8d8d8 60%,#7d7d6f)"></div><div class="lab">Fuel Delivery</div></div>
<div class="card" style="left:436px"><div class="ph" role="img" aria-label="Photo of shelves stocked with motor oil bottles" style="background:linear-gradient(180deg,#6b4a32,#3c5a9a 50%,#7a2a2a)"></div><div class="lab">Oil</div></div>
<div class="card" style="left:781px"><div class="ph" role="img" aria-label="Photo of white cylindrical farm fuel tanks" style="background:linear-gradient(180deg,#8e8a84,#e8e8e8 55%,#a9a79f)"></div><div class="lab">Farm Fuel</div></div>
<svg class="abs" style="left:572px;top:2186px" width="56" height="16"><circle cx="9" cy="8" r="6" fill="#333"/><circle cx="28" cy="8" r="6" fill="#333"/><circle cx="47" cy="8" r="5" fill="none" stroke="#333" stroke-width="1.5"/></svg>

<div class="abs employ" role="img" aria-label="Faded sepia photo of a diamond-plate truck bed"></div>
<h2 class="abs center" style="top:2352px"><span style="color:#6a5a44;font-weight:300">Employment</span> <em>Opportunities</em></h2>
<div class="abs center" style="top:2415px;font-size:21px;font-weight:500;color:#333">Career Opportunity</div>
<div class="abs center" style="top:2455px;font-size:17px;color:#444">Brandwyn Fuel Company is currently accepting resumes for the following postion (s):</div>
<div class="abs center" style="top:2500px;font-size:17px;color:#444">Brandwyn Fuel Company has no postions available at this time.</div>
<div class="btn-pill red" style="left:509px;top:2537px;width:182px">APPLY NOW <i></i></div>

<h2 class="abs center" style="top:2736px"><span style="font-weight:300;color:#555">Contact</span> <em>Brandwyn Fuel</em></h2>
<div class="field" style="left:162px;top:2818px;width:428px;height:40px">&#9679; First Name</div>
<div class="field" style="left:610px;top:2818px;width:428px;height:40px">&#9679; Last Name</div>
<div class="field" style="left:162px;top:2873px;width:428px;height:39px">&#9632; Company</div>
<div class="field" style="left:610px;top:2873px;width:428px;height:148px">&#9679; Message :</div>
<div class="field" style="left:162px;top:2927px;width:428px;height:36px">&#9993; Email Address</div>
<div class="field" style="left:162px;top:2981px;width:428px;height:40px">&#9742; Phone Number</div>
<div class="btn-pill red" style="left:497px;top:3053px;width:206px;height:55px;border-radius:28px;font-size:17px">SUBMIT <i></i></div>

<svg class="abs" style="left:0;top:3170px" width="1200" height="175" viewBox="0 0 1200 175"><path d="M0 120 C150 70 300 40 420 70 C520 100 580 150 700 135 C860 110 980 60 1200 80 L1200 175 L0 175Z" fill="#3e3e3e"/></svg>
<div class="abs footer"></div>
<div class="abs brand-name" style="left:450px;top:3460px;width:300px;font-size:26px;color:var(--white)">Brandwyn Fuel</div>
<div class="ficon" style="left:273px"><svg width="80" height="80"><path d="M40 22c-8 0-13 6-13 12 0 9 13 22 13 22s13-13 13-22c0-6-5-12-13-12z" fill="none" stroke="#fff" stroke-width="2"/><circle cx="40" cy="34" r="5" fill="none" stroke="#fff" stroke-width="2"/></svg></div>
<div class="ficon" style="left:558px"><svg width="80" height="80"><path d="M29 26c3-3 6 3 7 6s-3 4-1 7 5 6 8 6 4-4 7-2 5 5 2 7c-6 5-13 0-19-6s-8-14-4-18z" fill="none" stroke="#fff" stroke-width="2"/></svg></div>
<div class="ficon" style="left:851px"><svg width="80" height="80"><rect x="22" y="28" width="36" height="24" fill="none" stroke="#fff" stroke-width="2"/><path d="M22 28l18 14 18-14" fill="none" stroke="#fff" stroke-width="2"/></svg></div>
<div class="ftext" style="left:163px">418 Harlan Road,<br>Cedar Flats, TX 76299</div>
<div class="ftext" style="left:448px;top:3652px">Phone:<br>(555) 214-0187</div>
<div class="ftext" style="left:741px">Email:<br>info@brandwynfuel.com</div>
<div class="abs center flinks">Home &nbsp;|&nbsp; Our Company &nbsp;|&nbsp; Products &amp; Services &nbsp;|&nbsp; Contact Us &nbsp;|&nbsp; B's Containers &nbsp;|&nbsp; Employment Opportunities</div>
<div class="abs center copy">© Brandwyn Fuel 2019. All rights reserved</div>
<span class="soc" style="left:508px"></span>
<span class="soc" style="left:544px"></span>
<span class="soc" style="left:580px"></span>
<span class="soc" style="left:616px"></span>
</body>
</html>
```